holloway paving service

Needs to have phone number 0418259730 and email markholloway@brightmail.com.au.
ABN 62318470915
name mark holloway

For all your concreting solutions
Excavation
Exposed & colour concrete
House & shed slabs
Driveways
Landing & steps

Contact Information for Business Card

ph 0418259730
email markholloway@brightmail.com.au.
ABN 62318470915
name mark holloway

```html
<!DOCTYPE html>
<html lang="en">
<head>
<meta charset="utf-8">
<title>Holloway Paving Service — Business Card</title>
<link rel="stylesheet" href="https://fonts.googleapis.com/css2?family=Montserrat:wght@500;600;700&family=Open+Sans:wght@400;600&display=swap">
<style>
  :root {
    --orange: #f26722;
    --orange-dark: #e55d1a;
    --card-light: #efefef;
    --ink: #5a5a5a;
    --ink-soft: #8a8a8a;
    --rule: #9a9a9a;
    --backdrop: #d9d9d9;
    --white: #ffffff;
  }
  * { box-sizing: border-box; margin: 0; padding: 0; }
  html, body { width: 1200px; height: 896px; overflow: hidden; }
  body {
    background: var(--backdrop);
    font-family: "Open Sans", sans-serif;
    display: flex; flex-direction: column; align-items: center; justify-content: center;
    gap: 32px;
  }
  .card {
    position: relative; width: 700px; height: 400px; overflow: hidden;
    box-shadow: 0 10px 28px rgba(0,0,0,.18);
  }

  /* Front */
  .card--front { background: var(--card-light); color: var(--ink); }
  .front__band {
    position: absolute; left: 150px; top: -60px; width: 210px; height: 330px;
    background: rgba(0,0,0,.045); transform: skewX(-28deg);
  }
  .front__person { position: absolute; left: 46px; top: 150px; width: 260px; }
  .person__name {
    font-family: "Montserrat", sans-serif; font-weight: 600; font-size: 22px;
    letter-spacing: .5px; text-transform: uppercase; color: var(--ink);
    padding-bottom: 8px; border-bottom: 1.5px solid var(--rule);
  }
  .person__name .first { color: var(--orange); }
  .contact { list-style: none; margin-top: 10px; font-size: 15px; }
  .contact li { display: flex; align-items: center; gap: 8px; line-height: 1.55; }
  .contact svg { width: 13px; height: 13px; fill: var(--orange); flex: none; }

  .brand {
    position: absolute; display: flex; align-items: center; gap: 18px;
  }
  .brand__square { width: 62px; height: 62px; flex: none; }
  .brand__divider { width: 2px; height: 96px; flex: none; }
  .brand__name {
    font-family: "Montserrat", sans-serif; font-weight: 600; font-size: 21px;
    line-height: 1.25; letter-spacing: 1.5px; text-transform: uppercase;
  }
  .card--front .brand { left: 330px; top: 132px; }
  .card--front .brand__square { background: var(--ink); }
  .card--front .brand__divider { background: var(--orange); }
  .card--front .brand__name { color: var(--ink); }

  .front__abn {
    position: absolute; right: 40px; bottom: 40px; width: 260px;
    text-align: right; font-size: 15px; letter-spacing: .5px;
    padding-top: 10px; border-top: 1.5px solid var(--rule);
  }

  /* Back */
  .card--back { background: var(--orange); color: var(--white); }
  .back__band {
    position: absolute; left: 260px; top: -60px; width: 230px; height: 300px;
    background: var(--orange-dark); transform: skewX(-28deg); opacity: .7;
  }
  .card--back .brand { left: 300px; top: 48px; }
  .card--back .brand__square { background: var(--white); }
  .card--back .brand__divider { background: var(--white); }
  .card--back .brand__name { color: var(--white); }

  .back__tagline {
    position: absolute; left: 46px; top: 186px; width: 610px;
    font-size: 12.5px; letter-spacing: .6px; text-transform: uppercase;
    display: flex; align-items: center; gap: 14px;
  }
  .back__tagline::after { content: ""; flex: 1; height: 1px; background: rgba(255,255,255,.8); }
  .services { list-style: none; position: absolute; font-size: 16px; line-height: 1.5; }
  .services li { display: flex; align-items: center; gap: 9px; }
  .services li::before {
    content: ""; width: 8px; height: 8px; background: var(--white);
    transform: rotate(45deg); flex: none;
  }
  .services--main { left: 50px; top: 216px; }
  .services--extra { right: 56px; top: 272px; width: 240px; padding-bottom: 10px; border-bottom: 1px solid rgba(255,255,255,.8); }
</style>
</head>
<body>

  <section class="card card--front" aria-label="Business card front">
    <div class="front__band"></div>

    <div class="front__person">
      <p class="person__name"><span class="first">Mark</span> Holloway</p>
      <ul class="contact">
        <li>
          <svg viewBox="0 0 16 16" aria-hidden="true"><path d="M3 1h3l1.5 3.5-2 1.3a9 9 0 0 0 4.7 4.7l1.3-2L15 10v3a2 2 0 0 1-2 2A12 12 0 0 1 1 3a2 2 0 0 1 2-2z"/></svg>
          0418259730
        </li>
        <li>
          <svg viewBox="0 0 16 16" aria-hidden="true"><path d="M1 3h14v10H1zM2 4.2v.6l6 4 6-4v-.6L8 8z" fill-rule="evenodd"/></svg>
          markholloway@brightmail.com.au
        </li>
      </ul>
    </div>

    <div class="brand">
      <span class="brand__square"></span>
      <span class="brand__divider"></span>
      <p class="brand__name">Holloway Paving<br>Service</p>
    </div>

    <p class="front__abn">ABN 62318470915</p>
  </section>

  <section class="card card--back" aria-label="Business card back">
    <div class="back__band"></div>

    <div class="brand">
      <span class="brand__square"></span>
      <span class="brand__divider"></span>
      <p class="brand__name">Holloway Paving<br>Service</p>
    </div>

    <p class="back__tagline">For all your concreting solutions</p>

    <ul class="services services--main">
      <li>Excavation</li>
      <li>Exposed &amp; colour concrete</li>
      <li>House &amp; shed slabs</li>
    </ul>

    <ul class="services services--extra">
      <li>Driveways</li>
      <li>Landing &amp; steps</li>
    </ul>
  </section>

</body>
</html>
```